Marrowby Water Taxi and Transport Business Card

I need business cards for my new water taxi and freight transport business I have started here in Kodiak Alaska. Kodiak is a remote island in the middle of the gulf of Alaska. There are seven native villages around the island and Kodiak is the #2 fishing port in the United States. We also have the largest Coast Guard Base in the U.S. My company will be providing water taxi and freight transport logistics to the villages and many hunting and fishing lodges as well as remote properties around the island.

I would like a business card that isn't status quo, something that stands out, either in feel or appearance. I do like clean minimal designs but it needs to have the necessary contact info on it.

Target Market(s)

remote lodge / property owners, residents of the many villages around Kodiak and any one wanting to enjoy the great outdoors of Kodiak Alaska

Industry/Entity Type

Business

Contact Information for Business Card

I like clean simple designs that aren't cluttered but still provide the necessary information

Colors
0255a3
3277b5
33a4d5
9bcb3c
add136
fbed22
ffc214
f78f20
f37122

Requirements
Must have
• logo and contact info
• Captain Mason Elwick
• www.marrowbyferryline.com
• mason@marrowbyferryline.com

```html
<!DOCTYPE html>
<html lang="en">
<head>
<meta charset="utf-8">
<title>Marrowby Water Taxi and Transport – Business Card</title>
<link rel="stylesheet" href="https://fonts.googleapis.com/css2?family=Montserrat:wght@600&family=Questrial&display=swap">
<style>
  :root {
    --bg: #e9e6e1;
    --card: #ffffff;
    --navy: #0255a3;
    --mid-blue: #3277b5;
    --sky: #33a4d5;
    --deep: #0b2f66;
    --orange: #f78f20;
    --text: #555a60;
    --white: #ffffff;
  }
  * { box-sizing: border-box; margin: 0; padding: 0; }
  html, body {
    width: 1200px; height: 950px; overflow: hidden;
    background: var(--bg);
    font-family: "Questrial", sans-serif;
  }
  .sheet {
    width: 1200px; height: 950px;
    display: flex; flex-direction: column; align-items: center; justify-content: center;
    gap: 60px;
  }
  .card {
    position: relative;
    width: 700px; height: 400px;
    background: var(--card);
    overflow: hidden;
    box-shadow: 0 6px 18px rgba(0,0,0,.18);
  }

  /* Front */
  .front-photo {
    position: absolute; inset: 0;
    background:
      radial-gradient(ellipse at 60% 70%, rgba(180,215,240,.55), transparent 55%),
      linear-gradient(180deg, #3f86cc 0%, #2a66b0 35%, #1e4f93 60%, #3b7bc2 80%, #14386e 100%);
  }
  .front-brand {
    position: absolute; left: 0; right: 0; top: 150px;
    text-align: center; color: var(--white);
    font-size: 30px; line-height: 1.25; letter-spacing: 1px;
  }
  .social {
    position: absolute; left: 50%; top: 270px; transform: translateX(-50%);
    display: flex; gap: 12px;
  }
  .social span {
    width: 22px; height: 22px; border-radius: 50%;
    background: var(--white);
  }

  /* Back */
  .back-panel {
    position: absolute; right: 0; top: 0;
    width: 265px; height: 215px;
    background: radial-gradient(circle at 45% 30%, var(--sky) 0%, var(--mid-blue) 45%, var(--navy) 100%);
  }
  .back-brand {
    position: absolute; right: 0; top: 225px; width: 265px;
    display: flex; align-items: center; justify-content: center; gap: 10px;
    color: var(--navy); font-size: 24px; line-height: 1.2; text-align: left;
  }
  .back-brand .dot {
    width: 22px; height: 22px; border-radius: 50%; background: var(--orange); flex: none;
  }
  .person { position: absolute; left: 48px; top: 118px; }
  .person-name {
    font-family: "Montserrat", sans-serif; font-weight: 600;
    font-size: 26px; color: var(--navy); letter-spacing: .5px;
  }
  .person-role { font-size: 19px; color: var(--orange); margin-top: 2px; }
  .contact {
    position: absolute; left: 48px; top: 248px;
    font-size: 15px; color: var(--text); line-height: 22px; list-style: none;
  }
  .contact li { display: flex; align-items: center; gap: 8px; }
  .contact .plain { padding-left: 0; }
  .contact svg { width: 14px; height: 14px; fill: var(--navy); flex: none; }
</style>
</head>
<body>
<main class="sheet">

  <section class="card card-front">
    <div class="front-photo" role="img" aria-label="Photo of a boat wake on a blue Alaskan bay at dusk with mountains on the horizon"></div>
    <div class="front-brand">Marrowby<br>Water Taxi &amp; Transport</div>
    <div class="social" aria-label="Social links"><span></span><span></span><span></span></div>
  </section>

  <section class="card card-back">
    <div class="back-panel"></div>
    <div class="back-brand"><span class="dot"></span><span>Marrowby<br>Water Taxi &amp; Transport</span></div>

    <div class="person">
      <div class="person-name">MASON ELWICK</div>
      <div class="person-role">Captain</div>
    </div>

    <ul class="contact">
      <li class="plain">4120 Harbor Lane</li>
      <li class="plain">Marrowby, Alaska 39612</li>
      <li>
        <svg viewBox="0 0 24 24"><path d="M6.6 10.8a15 15 0 0 0 6.6 6.6l2.2-2.2a1 1 0 0 1 1-.25 11.4 11.4 0 0 0 3.6.57 1 1 0 0 1 1 1V20a1 1 0 0 1-1 1A17 17 0 0 1 3 4a1 1 0 0 1 1-1h3.5a1 1 0 0 1 1 1c0 1.25.2 2.45.57 3.57a1 1 0 0 1-.25 1z"/></svg>
        555 214 7093
      </li>
      <li>
        <svg viewBox="0 0 24 24"><path d="M2 5h20v14H2zm2 2v.5l8 5 8-5V7l-8 5z"/></svg>
        mason@marrowbyferryline.com
      </li>
      <li>
        <svg viewBox="0 0 24 24"><path d="M12 2a10 10 0 1 0 0 20 10 10 0 0 0 0-20zm6.9 6h-3a15.6 15.6 0 0 0-1.4-3.6A8 8 0 0 1 18.9 8zM12 4c.8 1.2 1.5 2.5 1.9 4h-3.8c.4-1.5 1.1-2.8 1.9-4zM4.3 14a8 8 0 0 1 0-4h3.4a16 16 0 0 0 0 4zm.8 2h3a15.6 15.6 0 0 0 1.4 3.6A8 8 0 0 1 5.1 16zm3-8h-3a8 8 0 0 1 4.4-3.6A15.6 15.6 0 0 0 8.1 8zM12 20c-.8-1.2-1.5-2.5-1.9-4h3.8c-.4 1.5-1.1 2.8-1.9 4zm2.3-6H9.7a14 14 0 0 1 0-4h4.6a14 14 0 0 1 0 4zm.2 5.6a15.6 15.6 0 0 0 1.4-3.6h3a8 8 0 0 1-4.4 3.6zm1.8-5.6a16 16 0 0 0 0-4h3.4a8 8 0 0 1 0 4z"/></svg>
        www.marrowbyferryline.com
      </li>
    </ul>
  </section>

</main>
</body>
</html>
```